RWT Fittings Ltd Business Cards

We need a business card with our business logo. We provide window and door installations on high-rises in west coast British Colombia, Canada.

I would like my business information and details on one side of the card, and the other side the company name with logo

Target Market(s)

General Contractors

Industry/Entity Type

Construction

Contact Information for Business Card

one side i want my company name and logo in the dark theme logo that i provided

Requirements
Must have
• Marco Peltieri, 16045518293, RWTFittings@mailbox-demo.com, 1407-5194 Linden Row Burnaby BC, V5H 2K9, Owner & Manager

```html
<!DOCTYPE html>
<html lang="en">
<head>
<meta charset="utf-8">
<title>RWT Fittings Ltd – Business Cards</title>
<link rel="stylesheet" href="https://fonts.googleapis.com/css2?family=Roboto:wght@400;500;700;900&display=swap">
<style>
  :root {
    --backdrop: #232323;
    --card: #1f2025;
    --accent: #29a8e0;
    --ink: #ffffff;
    --muted: #9a9a9a;
    --divider: #d9d9d9;
  }
  * { margin: 0; padding: 0; box-sizing: border-box; }
  html, body {
    width: 1200px; height: 780px; overflow: hidden;
    background: var(--backdrop);
    font-family: "Roboto", Arial, sans-serif;
  }
  .sheet {
    position: relative; width: 1200px; height: 780px;
    display: flex; align-items: center; justify-content: center; gap: 40px;
  }
  .card {
    position: relative; width: 540px; height: 310px;
    background: var(--card);
    box-shadow: 0 14px 30px rgba(0,0,0,.55);
    overflow: hidden;
  }

  /* Front: contact side */
  .accent-bar { position: absolute; width: 10px; background: var(--accent); }
  .accent-bar--left { left: 0; top: 150px; height: 140px; }
  .accent-bar--right { right: 0; top: 20px; height: 136px; }

  .brand {
    position: absolute; left: 40px; top: 112px; width: 200px;
    display: flex; align-items: center; gap: 10px;
    color: var(--accent); font-weight: 700; font-size: 22px; line-height: 1.1;
  }
  .brand__mark { width: 22px; height: 22px; background: var(--accent); flex: none; }

  .divider {
    position: absolute; left: 262px; top: 72px; width: 1px; height: 150px;
    background: var(--divider);
  }

  .person { position: absolute; left: 292px; top: 60px; }
  .person__name { font-size: 27px; font-weight: 900; color: var(--ink); letter-spacing: .2px; }
  .person__name .first { color: var(--accent); }
  .person__role { font-size: 13px; font-weight: 700; color: var(--ink); margin-top: 2px; }

  .contacts { list-style: none; margin-top: 18px; }
  .contacts li {
    display: flex; align-items: center; gap: 9px;
    font-size: 12.5px; color: var(--ink); margin-bottom: 6px;
  }
  .contacts svg { width: 14px; height: 14px; flex: none; }

  .address {
    position: absolute; left: 0; right: 0; bottom: 30px;
    text-align: center; font-size: 14px; color: var(--ink);
  }

  /* Back: brand side */
  .card--back { display: flex; align-items: center; justify-content: center; }
  .brand--large {
    position: static; width: auto; gap: 16px;
    font-size: 38px; color: var(--accent);
  }
  .brand--large .brand__mark { width: 38px; height: 38px; }
</style>
</head>
<body>
<main class="sheet">

  <section class="card card--front" aria-label="Business card, contact side">
    <span class="accent-bar accent-bar--left"></span>
    <span class="accent-bar accent-bar--right"></span>

    <div class="brand">
      <span class="brand__mark"></span>
      <span class="brand__name">RWT Fittings Ltd</span>
    </div>

    <span class="divider"></span>

    <div class="person">
      <h1 class="person__name"><span class="first">Marco</span> Peltieri</h1>
      <p class="person__role">Owner &amp; Manager</p>
      <ul class="contacts">
        <li>
          <svg viewBox="0 0 24 24" aria-hidden="true"><path fill="#29a8e0" d="M6.6 10.8a15 15 0 0 0 6.6 6.6l2.2-2.2a1 1 0 0 1 1-.25 11.4 11.4 0 0 0 3.6.57 1 1 0 0 1 1 1V20a1 1 0 0 1-1 1A17 17 0 0 1 3 4a1 1 0 0 1 1-1h3.5a1 1 0 0 1 1 1c0 1.25.2 2.45.57 3.57a1 1 0 0 1-.25 1z"/></svg>
          <span>1 604 551 8293</span>
        </li>
        <li>
          <svg viewBox="0 0 24 24" aria-hidden="true"><rect x="2" y="5" width="20" height="14" rx="1.5" fill="#29a8e0"/><path d="M3 6l9 7 9-7" fill="none" stroke="#1f2025" stroke-width="1.6"/></svg>
          <span>RWTFittings@mailbox-demo.com</span>
        </li>
      </ul>
    </div>

    <p class="address">1407-5194 Linden Row Burnaby BC, V5H 2K9</p>
  </section>

  <section class="card card--back" aria-label="Business card, brand side">
    <div class="brand brand--large">
      <span class="brand__mark"></span>
      <span class="brand__name">RWT Fittings Ltd</span>
    </div>
  </section>

</main>
</body>
</html>
```